KestrelCourse

Take the information and positional images that I have supplied (in the inDesign doc) and design a contemporary clean corporate brochure better than supplied. I would like an indesign or layered photoshop file back so that I can place the highres images in when I have finished and also the contact details when I get a number (not supplied) yet. I would like to use prussian blue and match it to other material that I am having made.

I'd like the design to be strong and dynamic as it is the first print run and will need sever other design concepts to compliment it. When one great and unique design comes through I am start with other brochures that fit in with it.

Its tailored to HR managers, but its an arts based training program so an element of visual sophistication would be advantageous.
Updates

Hi ........It will be printed on a matt eco/recycled card (which will absorb a lot of ink and be somewhat flat)

Dear Designers I am uploading some high res images to use in the layout which will be A5 6 page foldout. Thanks, have a great day!

Hi Designers, the design should be more than, and potentially different to what I supplied. It can be similar but I am actually looking for a more sophisticated design than what I suppled. Thank you.

Hi Designers, thanks so much for your designs so far. My feeling is that I may have confused the brief, I would prefer if the design was not the same as mine, the reason I have submitted my design to ArtMarketHub is so that I could have a different design. This brochure will go out to 3000 people so I want it to look strong and sophisticated. I am also going to create 4-5 other designs from this one to go in packs, so this design (its my first time with ArtMarketHub) needs to be strong so that everything else can be moulded against it. I haven't submitted the other briefs yet as it would be a waste of time until the first one is done. Thank you kindly.

Target Market(s)

Corporates & HR Managers

Industry/Entity Type

Training

Requirements
Must have
• Logo and prussian blue as a colour. An inDesign (CS5) file returned so I can drop hi res positionals in at a later stage.
Should not have
• Flattened files as details for this brochure are not finalised

```html
<!DOCTYPE html>
<html lang="en">
<head>
<meta charset="utf-8">
<title>KestrelCourse brochure</title>
<link rel="stylesheet" href="https://fonts.googleapis.com/css2?family=Jost:wght@400;500;600&family=Crimson+Text:ital@0;1&display=swap">
<style>
:root{
  --prussian:#1f4f8c;
  --prussian-deep:#163f74;
  --ink:#2a2a2a;
  --grey:#777;
  --paper:#ffffff;
  --mist:#e4e5e8;
  --stage:#000000;
}
*{box-sizing:border-box;margin:0;padding:0}
html,body{width:1200px;height:900px;overflow:hidden;background:var(--stage)}
body{font-family:"Jost",sans-serif;color:var(--ink)}
.brochure{position:absolute;left:60px;top:170px;width:1080px;height:560px;display:flex}
.panel{position:relative;width:360px;height:560px;overflow:hidden;background:var(--paper)}
.panel--inside{background:linear-gradient(90deg,#fff 0%,#f4f4f6 40%,#dcdde1 100%)}
.panel--cover{background:linear-gradient(180deg,#eeeff2 0%,#e3e4e8 60%,#d6d7dc 100%)}

.heading{font-family:"Jost",sans-serif;font-weight:400;color:var(--prussian);text-transform:uppercase;letter-spacing:.5px;line-height:1}
.heading strong{font-weight:600}

/* how it works */
.how{position:absolute;left:24px;top:18px;width:320px}
.how .heading{font-size:21px;margin-bottom:2px}
.how-box{background:var(--prussian-deep);color:#fff;border-radius:8px;padding:8px 10px 10px;font-size:8.2px;line-height:1.35}
.how-box b{font-weight:600}
.options{display:grid;grid-template-columns:56px 1fr;margin-top:6px}

.meetups{position:absolute;left:28px;top:170px;width:320px}
.meetups .heading{font-size:20px;display:flex;align-items:flex-end;gap:4px}
.meetups .heading::after{content:"";flex:1;height:2px;background:var(--prussian-deep);margin-bottom:2px}
.meetups .lead{font-size:10.5px;line-height:1.2;color:#333;margin-top:2px}
.lectures-title{font-weight:600;font-size:10.5px;text-transform:uppercase;margin:8px 0 3px}
.lectures{display:grid;grid-template-columns:1fr 1fr;gap:10px;font-size:7.6px;line-height:1.35;color:#333}

.photos{position:absolute;left:0;bottom:0;width:360px;height:160px;display:flex;gap:4px}
.photo{flex:1;background:linear-gradient(160deg,#3a2a22 0%,#14100e 70%)}
.photo--stage{background:linear-gradient(200deg,#2a2a2e 0%,#0b0b0c 60%)}

/* inside panel */
.corner-pattern{position:absolute;left:0;top:0;width:58px;height:52px;background:linear-gradient(135deg,var(--prussian) 0%,#6c86b8 100%);opacity:.85}
.intro{position:absolute;left:26px;top:34px;width:320px;font-size:7.6px;line-height:1.4;color:#444}
.brand-inline{font-family:"Jost",sans-serif;font-size:22px;color:var(--prussian);font-weight:400;margin-right:4px;vertical-align:-2px}
.intro p+p{margin-top:8px}

.tutor{position:absolute;left:26px;top:186px;width:320px}
.tutor .heading{font-size:20px;display:flex;align-items:flex-end;gap:3px;border-left:2px solid var(--prussian);padding-left:4px}
.tutor .heading::after{content:"";flex:1;height:2px;background:var(--prussian);margin-bottom:2px}
.bio{font-size:7.6px;line-height:1.4;color:#444;margin-top:3px}
.bio b{font-weight:600}

.quotes{position:absolute;left:26px;top:255px;width:320px;display:grid;grid-template-columns:146px 1fr;gap:14px}
.quote-main{border-left:2px solid var(--prussian);padding-left:8px;font-family:"Crimson Text",serif;font-style:italic;font-size:15.5px;line-height:1.2;color:#555}
.quote-main .mark{color:var(--prussian);font-size:26px;font-style:normal;line-height:.5;vertical-align:-6px}
.cite{font-family:"Jost",sans-serif;font-style:normal;font-size:6.8px;line-height:1.35;color:#444;margin-top:6px;text-transform:none}
.cite b{text-transform:uppercase;font-weight:500}
.quote-side{font-family:"Crimson Text",serif;font-style:italic;font-size:9px;line-height:1.25;color:#555;margin-bottom:14px}

.contact-bar{position:absolute;left:14px;bottom:18px;width:332px;height:22px;background:var(--prussian);border-radius:0 8px 8px 0;color:#e6ecf5;font-size:6.8px;display:flex;align-items:center;padding-left:14px;gap:6px}

/* cover */
.cover-pattern{position:absolute;left:0;top:0;width:360px;height:300px;background:radial-gradient(ellipse at 50% 30%,#2d4fa3 0%,#4766b4 45%,#b8c3df 80%,rgba(228,229,232,0) 100%)}
.cover-quote{position:absolute;left:34px;top:318px;width:300px;text-align:center;font-family:"Crimson Text",serif;font-style:italic;font-size:17px;line-height:1.2;color:#666}
.cover-quote .mark{color:#8d95a8;font-size:34px;font-style:normal;line-height:.4;vertical-align:-10px}
.cover-quote cite{display:block;font-family:"Jost",sans-serif;font-style:normal;font-size:8px;letter-spacing:1px;color:#888;text-align:right;margin-top:4px;padding-right:50px}
.brand-card{position:absolute;left:52px;top:410px;width:254px;height:96px;background:var(--prussian);border-radius:8px 8px 0 0;display:flex;align-items:center;justify-content:center;gap:10px}
.brand-card .square{width:18px;height:18px;background:#fff}
.brand-name{font-family:"Jost",sans-serif;font-size:30px;font-weight:400;color:#fff;letter-spacing:.5px}
</style>
</head>
<body>
<main class="brochure">

  <section class="panel panel--program">
    <div class="how">
      <h2 class="heading">How it <strong>works</strong></h2>
      <div class="how-box">
        <p>The <b>KESTRELCOURSE</b> runs from your boardroom minimising collective travel time. We work with a group of 5 people per session (you can hold multiple sessions over different days). There are 12 hours of group/tuition time that can be factored in to suit your business environment accommodating how long you can engage your team in training.</p>
        <div class="options">
          <span>Choose from:</span>
          <span>2 hours over 6 weeks; or<br>3 hours over 4 weeks; or<br>6 hours over 2 weeks</span>
        </div>
      </div>
    </div>

    <div class="meetups">
      <h2 class="heading"><strong>Meet</strong>&nbsp;ups</h2>
      <p class="lead">Meetups are an engaging way to satisfy your teams need for socialisation. Meetups run for one hour and can allow participation of up to 100 people.</p>
      <h3 class="lectures-title">Lunchtime &amp; afternoon lectures</h3>
      <div class="lectures">
        <p>We will come to your boardroom and spend time together involving your staff in a visually rich, culturally engaging discussion of the many of histories of art and photography with particular reference to Australian context, ignighting debate, and facilitating participation and life enriching skills.</p>
        <p>The lectures run for one hour and organisations are encouraged to allow time for group social participation after the talks to allow staff to engage with each other, reflecting on the talk, expressing their own opinions, listening to others while learning great good stuff in the process.</p>
      </div>
    </div>

    <div class="photos">
      <div class="photo" role="img" aria-label="Photo of a speaker presenting to a seated audience in a dim hall"></div>
      <div class="photo photo--stage" role="img" aria-label="Photo of the tutor speaking at a lectern with a laptop"></div>
    </div>
  </section>

  <section class="panel panel--inside">
    <div class="corner-pattern" role="img" aria-label="Small cluster of overlapping rounded squares pattern"></div>
    <div class="intro">
      <p><span class="brand-inline">lumenworks</span>is a unique concept whereby we will come to your premises and teach your staff the fundamentals of photography with emphasis on personal and interpersonal development within a group environment.</p>
      <p>The learning programs we run are both artistic and holistic in nature. The study of art and photography within the work place builds self confidence and enhances motivation and enthusiasm especially given photography is an integral part of all of our lives. Students learn together and have the opportunity to develop individual forms of self expression in their own time, increasing self awareness. As they rejoin and express their individuality, healthier relationships and bonding with colleagues develop.</p>
    </div>

    <div class="tutor">
      <h2 class="heading">Your&nbsp;<strong>Tutor</strong></h2>
      <p class="bio"><b>MARA ELLISON</b> holds a Masters Degree in Visual Art, majoring in PhotoMedia from Harbour College of Fine Arts, Eastbay University. Mara has been lecturing &amp; mentoring for over a decade in art, photography, creative and personal development.</p>
    </div>

    <div class="quotes">
      <blockquote class="quote-main">
        <span class="mark">&ldquo;</span> Mara has a great knowledge of her subject and is very enthusiastic in her teaching methodology. She is able to produce high quality results from both beginning students as well as from more mature students.&rdquo;
        <p class="cite"><b>— Tobias Renner</b><br>Chair of PhotoMedia<br>Harbour College of Fine Arts,<br>Eastbay University (May 2011)</p>
      </blockquote>
      <div>
        <blockquote class="quote-side">&ldquo;On a personal level, I have found Mara an absolute joy to work with and she has become a mentor for me.&rdquo;
          <p class="cite"><b>— Grant Whitley</b><br>Associate Director<br>Creative Learning<br>The Coastal Centre for Photography</p>
        </blockquote>
        <blockquote class="quote-side">&ldquo;I noticed a marked difference in the compatibility of my team almost immediately.&rdquo;
          <p class="cite"><b>— Lena Hart</b><br>Director, Tidemark</p>
        </blockquote>
        <blockquote class="quote-side">&ldquo;Very clever and outstanding technique for motivating staff and encouraging teambuilding.&rdquo;
          <p class="cite"><b>— Owen Crane</b><br>Norvell Australia</p>
        </blockquote>
      </div>
    </div>

    <footer class="contact-bar">
      <span>12 Larkin St Elmwood NSW 2099</span><span>|</span><span>www.lumenworks.me</span><span>|</span><span>info@lumenworks.me</span><span>|</span><span>0400 000 123</span>
    </footer>
  </section>

  <section class="panel panel--cover">
    <div class="cover-pattern" role="img" aria-label="Decorative pattern of nested blue rounded squares"></div>
    <blockquote class="cover-quote">
      <span class="mark">&ldquo;</span> The strength of the team is each individual member. The strength of each member is the team. <span class="mark">&rdquo;</span>
      <cite>— DALE PORTER</cite>
    </blockquote>
    <div class="brand-card">
      <span class="square"></span>
      <span class="brand-name">lumenworks</span>
    </div>
  </section>

</main>
</body>
</html>
```